Cleaning service website design

We need a new nice web design(logo will be the same) for a new cleaning service Company:

Informations about Company and logo you can take from flyers in attachments.

This is a cleaning service Company which have simple rules and we would like to show that(in checklist form) on website:

- What we do and that we're Cleaning Green

- Why us?

- How much(our pricing is simple)

Also we would like to communicate with clients by some nice/big pictures on website and the most important thing is our phone number and short/fast Brimtallow.

Also there should be some space for description about our Company.

Generally all information on main page can be short: about us, about service(what we do), last reviews, tips (for example: Tip of the week) and other can be some introduction to subpage where will be more information.

There will be few subpages like: About us, About our service, Photos(Before and after), Reviews , Tips, FAQ, Contact, Looking for a Job? - most of them will be just text so you can project just one example.

```html
<!DOCTYPE html>
<html lang="en">
<head>
<meta charset="utf-8">
<title>Tidy Nest – Cleaning Service</title>
<link href="https://fonts.googleapis.com/css2?family=Ubuntu:ital,wght@0,400;0,500;0,700;1,400;1,500;1,700&display=swap" rel="stylesheet">
<style>
:root{
  --blue:#0b63c4;
  --blue-dark:#0a56ad;
  --green:#5cb85c;
  --green-text:#3f9f2f;
  --green-light:#8fd07d;
  --yellow:#f5f000;
  --text:#444;
  --muted:#666;
  --panel:#f4f4f4;
  --border:#d6d6d6;
  --footer:#e4e4e4;
}
*{margin:0;padding:0;box-sizing:border-box}
html,body{width:1097px;height:1200px;overflow:hidden}
body{position:relative;background:#fff;font-family:'Ubuntu',sans-serif;color:var(--text)}
.abs{position:absolute}
.header-band{left:0;top:0;width:1097px;height:135px;background:linear-gradient(#fff,#ececec)}
.brand{left:119px;top:20px;display:flex;align-items:center;gap:10px;font-size:30px;font-weight:700;color:var(--blue)}
.brand-dot{width:22px;height:22px;border-radius:50%;background:var(--green)}
.call{left:786px;top:40px;display:flex;gap:10px;align-items:center}
.call-label{font-size:16px;font-weight:500;color:var(--blue);line-height:18px}
.call-number{font-size:24px;font-weight:500;color:var(--green);line-height:28px}
.nav{left:119px;top:114px;width:859px;height:40px;background:var(--blue);border-radius:3px;display:flex;overflow:hidden}
.nav a{color:#fff;text-decoration:none;font-size:12.5px;font-weight:500;line-height:40px;padding:0 17px;white-space:nowrap}
.nav a.active{background:var(--green)}
.nav a+a{margin-left:4px}
.hero{left:119px;top:160px;width:859px;height:353px;border-radius:3px;background:linear-gradient(90deg,#5cad55,#8fd27e 55%,#5fae56);overflow:hidden}
.hero h1{position:absolute;left:27px;top:36px;font-size:37px;line-height:42px;font-weight:700;font-style:italic;color:#fff}
.supplies{position:absolute;left:24px;top:130px;width:78px;height:90px;border-radius:10px;background:linear-gradient(#6d7fb8,#2f3f86)}
.offer{position:absolute;left:113px;top:132px;color:var(--yellow);font-style:italic;font-size:25px}
.as-low{position:absolute;left:113px;top:170px;color:#fff;font-style:italic;font-size:15px}
.price{position:absolute;left:182px;top:168px;color:var(--yellow);font-style:italic;font-size:78px;line-height:80px}
.price span{font-size:40px;color:#fff;vertical-align:top;line-height:60px;margin-right:4px}
.quote-btn{position:absolute;left:28px;top:260px;width:174px;height:35px;background:linear-gradient(#fff,#e6e6e6);border-radius:3px;font-size:17px;font-weight:500;color:#333;text-align:center;line-height:35px}
.dots{position:absolute;left:20px;top:324px;display:flex;gap:5px}
.dots i{width:12px;height:12px;border-radius:50%;background:#e2e2e2}
.dots i:first-child{background:var(--blue)}
.team-photo{position:absolute;left:356px;top:0;width:503px;height:353px;background:linear-gradient(180deg,rgba(40,40,40,0) 0%,rgba(40,40,50,.35) 55%,rgba(30,40,90,.5) 100%)}
.heading{font-size:21px;color:var(--blue);font-weight:400}
.about-photo{left:119px;top:574px;width:201px;height:146px;border:1px solid var(--border);background:linear-gradient(#8ab7e4,#c7d9ea 45%,#4f5a62)}
.about-text{left:338px;top:570px;width:412px;font-size:11.8px;line-height:16.5px;color:var(--muted)}
.btn{display:inline-block;background:var(--green);color:#fff;font-size:11.5px;font-weight:500;border-radius:3px;text-align:center;line-height:26px;height:26px}
.divider{left:119px;top:752px;width:640px;height:1px;background:#ddd}
.panel{background:var(--panel);border:1px solid var(--border)}
.whatwedo{left:777px;top:574px;width:201px;height:235px}
.whatwedo ul{list-style:none;position:absolute;left:12px;top:14px;width:180px}
.whatwedo li{position:relative;padding-left:19px;font-size:11.5px;line-height:16.5px;color:var(--text);margin-bottom:7.3px}
.whatwedo li::before{content:"";position:absolute;left:1px;top:5px;width:7px;height:7px;border-radius:50%;background:var(--green)}
.box{top:775px;width:308px;height:291px}
.box h2{position:absolute;left:19px;top:12px}
.entry{position:absolute;left:19px;width:266px;display:flex;gap:14px}
.thumb{width:59px;height:52px;flex:none;border:1px solid #ccc}
.entry h3{font-size:13px;font-weight:500;color:var(--green-text);line-height:17px}
.entry p{font-size:11.3px;line-height:16.5px;color:var(--text)}
.entry .posted{font-size:10.5px;font-style:italic;color:var(--blue);margin-top:4px}
.sep{position:absolute;left:19px;width:266px;height:1px;background:#ddd}
.client{left:777px;top:824px;width:201px;height:243px}
.client blockquote{position:absolute;left:14px;top:40px;width:178px;font-size:11.3px;line-height:18.3px;font-style:italic;color:var(--muted)}
.client .by{position:absolute;left:14px;top:178px;font-size:13px;font-weight:500;color:var(--green-text)}
.footer{left:0;top:1088px;width:1097px;height:112px;background:var(--footer)}
.footer-links{left:119px;top:1107px;font-size:11.5px;color:var(--muted);word-spacing:1px}
.copy{left:119px;top:1145px;font-size:11.5px;line-height:17.5px;color:var(--muted)}
.copy span{color:var(--blue)}
.social{left:813px;top:1129px;display:flex;gap:6px}
.social i{width:28px;height:28px;border-radius:3px}
</style>
</head>
<body>
<div class="abs header-band"></div>
<div class="abs brand"><span class="brand-dot"></span>Tidy Nest</div>
<div class="abs call">
  <svg width="30" height="38" viewBox="0 0 30 38" aria-hidden="true"><path d="M8 3c-3 1-6 4-5 10 1 8 7 17 14 21 4 2 7 1 9-1l1-2-6-6-3 2c-3-2-6-7-7-11l3-2-3-8z" fill="#c9302c"/></svg>
  <div><div class="call-label">Call Us Today:</div><div class="call-number">555-014-2280</div></div>
</div>
<nav class="abs nav">
  <a class="active">Home</a><a>About Us</a><a>Our Service</a><a>Photos Gallery</a><a>Reviews</a><a>Tips</a><a>FAQ</a><a>Contact Us</a><a>Looking for a Job?</a>
</nav>

<section class="abs hero">
  <div class="team-photo" role="img" aria-label="Smiling team of four cleaners in yellow gloves holding cleaning supplies"></div>
  <h1>Affordably Simpler<br>Making your Life</h1>
  <div class="supplies" role="img" aria-label="Bucket of cleaning supplies with a mop"></div>
  <div class="offer">House Cleaning</div>
  <div class="as-low">as low as</div>
  <div class="price"><span>$</span>79</div>
  <div class="quote-btn">Get A Free Quote</div>
  <div class="dots"><i></i><i></i><i></i><i></i></div>
</section>

<h2 class="abs heading" style="left:119px;top:535px">About Our Company</h2>
<div class="abs about-photo" role="img" aria-label="Portrait of the company owners outdoors"></div>
<div class="abs about-text">
  <p>We are Daniel and Marta Kowalewski and we have personally experienced the struggle of finding a reliable and affordable maid service. We understand how busy life can be and cleaning is one of the tasks that falls off the list when you're stretched too thin. We are here to help! Let Tidy Nest take care of the house cleaning so you can focus on the more important things in life. Halton, Burlington, Oakville and Milton residents can count on us to make your home sparkle from top to bottom!</p>
  <span class="btn" style="width:64px;margin-top:9px">MORE</span>
</div>

<h2 class="abs heading" style="left:777px;top:535px">What We Do</h2>
<div class="abs panel whatwedo">
  <ul>
    <li>Making mirrors shine</li>
    <li>Mop or vacuum your floors</li>
    <li>Dust surfaces</li>
    <li>Collect garbage</li>
    <li>Make beds</li>
    <li>Cleaning of hardwood/ tile/ linoleum floors</li>
  </ul>
  <span class="btn abs" style="left:14px;top:192px;width:64px">MORE</span>
</div>

<div class="abs divider"></div>

<section class="abs panel box" style="left:120px">
  <h2 class="heading">Last Reviews</h2>
  <div class="entry" style="top:48px">
    <div class="thumb" role="img" aria-label="Reviewer photo" style="background:linear-gradient(#e8e2da,#6b5644)"></div>
    <div><h3>Paula Wren</h3><p>Nunc dignissim lectus vitae eros placerat euismod. Aenean lacinia sodales eros....</p><p class="posted">Posted on 3 days ago</p></div>
  </div>
  <div class="sep" style="top:143px"></div>
  <div class="entry" style="top:154px">
    <div class="thumb" role="img" aria-label="Reviewer photo" style="background:linear-gradient(#dfe7ee,#c9a78b)"></div>
    <div><h3>Paula Wren</h3><p>Nunc dignissim lectus vitae eros placerat euismod. Aenean lacinia sodales eros....</p><p class="posted">Posted on 3 days ago</p></div>
  </div>
  <span class="btn abs" style="left:18px;top:256px;width:64px">READ ALL</span>
</section>

<section class="abs panel box" style="left:451px">
  <h2 class="heading">Tips of the day</h2>
  <div class="entry" style="top:48px">
    <div class="thumb" role="img" aria-label="Vacuum cleaner on a floor" style="background:linear-gradient(#d9d9d9,#6c6c6c)"></div>
    <div><h3>Morbi iaculis fringilla gravida..</h3><p>Aenean a nibh eget turpis vehicula tempus ac sed massa.</p></div>
  </div>
  <div class="sep" style="top:115px"></div>
  <div class="entry" style="top:131px">
    <div class="thumb" role="img" aria-label="Cleaner wiping a surface in yellow gloves" style="background:linear-gradient(#f2f2f2,#e6dc5a)"></div>
    <div><h3>Morbi iaculis fringilla gravida..</h3><p>Aenean a nibh eget turpis vehicula tempus ac sed massa.</p></div>
  </div>
  <div class="sep" style="top:198px"></div>
  <div class="entry" style="top:213px">
    <div class="thumb" role="img" aria-label="Yellow gloves cleaning a window" style="background:linear-gradient(#2b4f8a,#e4d832)"></div>
    <div><h3>Morbi iaculis fringilla gravida..</h3><p>Aenean a nibh eget turpis vehicula tempus ac sed massa.</p></div>
  </div>
</section>

<section class="abs panel client">
  <h2 class="heading abs" style="left:12px;top:10px">Client Says...</h2>
  <blockquote>Vestibulum vel metus sit amet turpis bibendum tincidunt vel sit amet quam. Pellentesque habitant morbi tristique senectus et netus et malesuada fames ac turpis eges-tas. Nunc consequat congue nulla eu imperdiet...</blockquote>
  <div class="by">By Owen Hale</div>
  <span class="btn abs" style="left:124px;top:205px;width:64px">READ ALL</span>
</section>

<footer>
  <div class="abs footer"></div>
  <div class="abs footer-links">Home &nbsp;|&nbsp; About Us &nbsp;|&nbsp; Our Service &nbsp;|&nbsp; Photos Gallery &nbsp;|&nbsp; Reviews &nbsp;|&nbsp; Tips &nbsp;|&nbsp; FAQ &nbsp;|&nbsp; Contact &nbsp;|&nbsp; Looking for a Job?</div>
  <div class="abs copy">Copyright © 2013. <span>HaltonTidyNest.</span><br>All Right Reserved</div>
  <div class="abs social" aria-label="Social links">
    <i style="background:#3b5b9a"></i><i style="background:#5bc6e8"></i><i style="background:#1b78b0"></i><i style="background:#f08a1c"></i><i style="background:#c4242b"></i>
  </div>
</footer>
</body>
</html>
```